Awsome new website

We are a Fencing Contracting company in Melbourne Australia. We supply and install Timer and Steel boundary fences as well as Pool fencing (e.g. glass, tubular steel). We also manufacture and install swing and sliding gates.

We want a new website that is a modern business website.
We are targeting domestic and business clients.
The design should compliment our logo and company name.
The website needs to be easy to update.

Some specifics we want.
Menu - Main menu at top of page and smaller footer menu (to add different menu items)
Slider - Main page to have a slider on it that's easy for us to add and remove slides.
Call to action - all pages to have a "call to action" logo or icon that attracts attention (see file "call_to_action.pdf)
Instant quote - we have a online quote page we need a distinctive logo or icon to redirect to this page.
Main page to have a product /Service guide (see file "website_idea.jpg")
Main page to have widgets or quick link to
o why choose us
o Brochures
o Gallery

Have a Gallery page formatted with different category galleries. e.g. Timber, Glass, Feature
Maintain the current link to our staff page with password, (link in footer menu)

Hopefully that covers everything.
Our current website is www.tallgumfencing.com.au to have a look at the current site.
regards Doug

• Turn off blogging as we don’t want 100’s of comments from spammers to delete

We would like to implement the Portalio plugin (see "http://portalio-plug.net/" ), but this can be done after the new Theme has been implemented.

```html
<!DOCTYPE html>
<html lang="en">
<head>
<meta charset="utf-8">
<title>Tall Gum Fencing</title>
<link href="https://fonts.googleapis.com/css2?family=Montserrat:wght@300;400;600;700&family=Open+Sans:wght@400;600&family=Oswald:wght@600&family=Roboto+Condensed:wght@700&display=swap" rel="stylesheet">
<style>
:root{
  --red:#d3121b;
  --red-dark:#a80a12;
  --maroon:#5e0508;
  --ink:#333;
  --muted:#666;
  --page:#f1f1f1;
  --band:#e6e6e6;
  --yellow:#f7d51a;
  --white:#fff;
}
*{box-sizing:border-box;margin:0;padding:0}
html,body{width:693px;height:1200px;overflow:hidden}
body{position:relative;background:var(--page);font-family:"Open Sans",Arial,sans-serif;color:var(--ink)}
.abs{position:absolute}
.logo{left:81px;top:18px;width:110px;height:36px;background:var(--white);border:2px solid var(--red);display:flex;align-items:center;justify-content:center;gap:5px;font:700 11px "Montserrat",sans-serif;color:var(--red)}
.logo i{width:8px;height:8px;background:var(--red);display:block}
.call{left:451px;top:25px;font:400 10px "Montserrat",sans-serif;color:var(--muted)}
.call strong{display:block;font:600 15px "Montserrat",sans-serif;color:var(--red);margin-top:1px}
.agent-photo{left:566px;top:5px;width:58px;height:65px;border-radius:30px 30px 0 0;background:linear-gradient(#e7d6cc,#c9b4a8)}
.nav{left:0;top:71px;width:693px;height:26px;background:linear-gradient(#e82128,#b70c14);display:flex;padding-left:81px}
.nav a{color:var(--white);font:600 9.5px "Montserrat",sans-serif;text-decoration:none;line-height:26px;padding:0 17px;border-right:1px solid rgba(0,0,0,.2)}
.nav a:first-child{padding-left:17px;border-left:1px solid rgba(0,0,0,.2)}
.nav a:last-child{border-right:0}
.slider{left:81px;top:107px;width:531px;height:235px;background:var(--white);box-shadow:0 1px 4px rgba(0,0,0,.2);padding:8px 7px}
.slide-photo{width:517px;height:220px;background:linear-gradient(#c8dcea 0%,#6cb3c9 30%,#3f95ab 50%,#8a5a33 70%,#b07a46 100%)}
.arrow{top:207px;width:19px;height:19px;background:rgba(200,30,30,.75);display:flex;align-items:center;justify-content:center}
.caption{left:120px;top:268px;width:450px;text-align:center;font:600 21px/24px "Oswald",sans-serif;color:var(--red-dark);-webkit-text-stroke:0.6px var(--white);letter-spacing:.3px}
.widget{top:363px;width:164px;height:178px;background:#f8f8f8;box-shadow:0 1px 3px rgba(0,0,0,.18)}
.widget h3{height:22px;background:linear-gradient(#e82128,#b70c14);color:var(--white);font:600 11px/22px "Montserrat",sans-serif;padding-left:7px}
.widget .thumb{margin:1px 9px 0;height:70px;border:2px solid var(--white);box-shadow:0 0 2px rgba(0,0,0,.3)}
.widget p{font-size:7.4px;line-height:11.3px;color:var(--muted);margin:13px 10px 0}
.pill{display:inline-block;margin:6px 0 0 10px;height:11px;padding:0 16px 0 6px;border-radius:6px;background:#ddd;font:600 5.5px/11px "Montserrat",sans-serif;color:#555;position:relative}
.pill::after{content:"";position:absolute;right:3px;top:2px;width:7px;height:7px;border-radius:50%;background:#555}
.welcome{left:81px;top:562px;width:345px}
.welcome h1{font:300 15px "Montserrat",sans-serif;color:#555;line-height:16px}
.welcome h1 span{display:block;font-weight:600;font-size:17px;color:var(--red);line-height:22px}
.welcome p{font-size:7.6px;line-height:12.1px;color:#444;margin-top:6px}
.welcome a{color:var(--red);text-decoration:none}
.services-title{left:81px;top:729px;font:400 12px "Montserrat",sans-serif;color:#222}
.service{width:175px;height:20px;border-radius:10px 0 0 10px;background:linear-gradient(90deg,#ecd5cc,#f4e4de 60%,rgba(241,241,241,0));font-size:8.3px;line-height:20px;padding-left:17px;color:#333}
.service::before{content:"";position:absolute;left:5px;top:7px;border-left:5px solid #c8a296;border-top:3px solid transparent;border-bottom:3px solid transparent}
.newsletter{left:450px;top:563px;width:161px;height:84px;background:linear-gradient(#dd1720,#b80c14);border:2px solid var(--white);box-shadow:0 1px 3px rgba(0,0,0,.25);padding:7px 10px;color:var(--white)}
.newsletter h4{font:600 12px "Montserrat",sans-serif;color:var(--yellow)}
.newsletter p{font-size:7px;line-height:9px}
.field{margin-top:6px;display:flex;height:20px}
.field span{flex:1;background:var(--white);font-size:7px;line-height:20px;color:#888;padding-left:6px}
.field b{width:28px;background:var(--yellow);font:700 9px/20px "Montserrat",sans-serif;color:#222;text-align:center}
.quote-card{left:450px;top:675px;width:161px;height:92px;background:#fafafa;box-shadow:0 1px 3px rgba(0,0,0,.2)}
.quote-figure{left:530px;top:660px;width:75px;height:88px;background:linear-gradient(#d7d7d7,#585d66)}
.quote-icon{left:472px;top:702px;width:25px;height:25px;background:var(--red);border-radius:3px;display:flex;align-items:center;justify-content:center}
.quote-bar{left:456px;top:748px;width:149px;height:16px;background:linear-gradient(#d01018,#9f080f);border-radius:2px;color:var(--white);font:600 8px/16px "Montserrat",sans-serif;padding-left:8px}
.quote-bar::after{content:"";position:absolute;right:5px;top:4px;width:8px;height:8px;border-radius:50%;background:#eee}
.contact{left:450px;top:780px;width:161px;height:121px;background:linear-gradient(#ffe45a,#f2c80f);box-shadow:0 2px 3px rgba(0,0,0,.2);text-align:center}
.contact h4{background:linear-gradient(#f3c50c,#e4ad06);height:24px;font:600 10.5px/24px "Montserrat",sans-serif;color:var(--white);padding-left:18px}
.contact .lead{font:600 8.5px/13px "Montserrat",sans-serif;color:var(--red);margin-top:11px}
.contact .small{font-size:7.5px;margin-top:8px;color:#222}
.contact .phone{font:700 18px "Roboto Condensed",sans-serif;color:#111;margin-top:2px}
.testimonials{left:0;top:918px;width:693px;height:190px;background:var(--band)}
.testimonials h2{position:absolute;left:81px;top:16px;font:400 11.5px "Montserrat",sans-serif;color:#222;letter-spacing:.3px}
.bubble{top:962px;width:255px;height:71px;background:#dcdcdc;border-radius:3px;padding:12px 20px 0 28px}
.bubble::after{content:"";position:absolute;left:30px;bottom:-8px;border-top:8px solid #dcdcdc;border-right:10px solid transparent}
.bubble h5{font:400 7.5px "Montserrat",sans-serif;color:#333}
.bubble p{font-size:7.5px;line-height:11.5px;color:#555;margin-top:2px}
.quote-mark{position:absolute;font:700 22px Georgia,serif;color:#bbb;line-height:1}
.avatar{top:1045px;width:46px;height:46px;border-radius:50%;background:#e6cfc6;border:3px solid #d9b8ab;display:flex;align-items:center;justify-content:center}
.avatar div{width:32px;height:32px;border-radius:50%;background:linear-gradient(#c7c1bd,#3b4150)}
.client{top:1062px;font:400 7px "Montserrat",sans-serif;color:var(--red)}
.footer{left:0;top:1108px;width:693px;height:92px;background:var(--maroon)}
.seal{left:83px;top:1121px;width:69px;height:69px;border-radius:50%;background:#e74a52;border:3px solid #f2b1b4}
.follow{left:196px;top:1122px;color:var(--white)}
.follow h4{font:600 10px "Montserrat",sans-serif;margin-bottom:4px}
.follow li{list-style:none;font-size:7.5px;line-height:18px;display:flex;align-items:center;gap:7px}
.follow li i{width:8px;height:8px;border-radius:50%;background:#f1d9d9;display:block}
.foot-nav{left:287px;top:1138px;display:flex;gap:12px}
.foot-nav a{color:var(--white);font-size:7.5px;text-decoration:none}
.copy{left:287px;top:1157px;color:#f1d9d9;font-size:7.5px}
</style>
</head>
<body>

<header>
  <div class="abs logo"><i></i>Tall Gum Fencing</div>
  <div class="abs call">Call NOW!<strong>(03) 9024-7716</strong></div>
  <div class="abs agent-photo" role="img" aria-label="Photo of a smiling support agent with a headset"></div>
</header>

<nav class="abs nav">
  <a href="#">HOME</a><a href="#">STEELSHADE</a><a href="#">INSTANT QUOTE</a><a href="#">GALLERY</a><a href="#">PRODUCTS &amp; SERVICES</a><a href="#">CONTACT US</a>
</nav>

<section class="abs slider">
  <div class="slide-photo" role="img" aria-label="Photo of a timber deck with railing and sun loungers overlooking a turquoise bay"></div>
</section>
<div class="abs arrow" style="left:99px"><svg width="8" height="10"><path d="M7 0 0 5l7 5z" fill="#fff"/></svg></div>
<div class="abs arrow" style="left:574px"><svg width="8" height="10"><path d="M1 0l7 5-7 5z" fill="#fff"/></svg></div>
<div class="abs caption">LOREM IPSUM IS SIMPLY DUMMY<br>TEXTOF THE PRINTING.</div>

<article class="abs widget" style="left:81px">
  <h3>WHY CHOOSE US</h3>
  <div class="thumb" role="img" aria-label="Photo of a house with a white picket fence" style="background:linear-gradient(#c9d9e6,#a7b59a 60%,#f4f4f4)"></div>
  <p>We offer a 12 month workmanship warranty on our fences and will clean the site for free of any fencing debris from the fence construction...</p>
  <span class="pill">READ MORE</span>
</article>
<article class="abs widget" style="left:265px">
  <h3>BROCHURES</h3>
  <div class="thumb" role="img" aria-label="Photo of fanned-out colour swatch cards" style="background:linear-gradient(120deg,#f5d33a,#f07b2f 35%,#e33b8e 60%,#7a56c9 85%)"></div>
  <p>We offer a 12 month workmanship warranty on our fences and will clean the site for free of any fencing debris from the fence construction...</p>
  <span class="pill">DOWNLOAD</span>
</article>
<article class="abs widget" style="left:448px">
  <h3>GALLERY</h3>
  <div class="thumb" role="img" aria-label="Photo of a modern house with glass balcony fencing" style="background:linear-gradient(#cfe0ee,#d8cbb8 55%,#8c7b6a)"></div>
  <p>We offer a 12 month workmanship warranty on our fences and will clean the site for free of any fencing debris from the fence construction...</p>
  <span class="pill">OUR WORK</span>
</article>

<section class="abs welcome">
  <h1>WELCOME TO<span>TALL GUM FENCING</span></h1>
  <p>Thank you for visiting us at Tall Gum Fencing, my name is Doug and I am the Manager.<br>I built my first fence when I was in my early twenties and have been building fences ever since. Over the last few years we have spent the time looking for fantastic fencing contractors to join our team. Because we only accept the best we have built our business to be one of Victoria's largest fencing contractors.</p>
  <p style="margin-top:12px">At Tall Gum Fencing, we believe in quality above all. The first fence we constructed was over 25 years ago and the number one thing we have learnt is that to do the job right the first time is the best insurance against costly rework.....<a href="#">[Read More]</a></p>
</section>

<h2 class="abs services-title">NEW SERVICES LIST</h2>
<div class="abs service" style="left:81px;top:752px">Bathroom Remodeling</div>
<div class="abs service" style="left:81px;top:782px">Attic &amp; Garage Finishing</div>
<div class="abs service" style="left:81px;top:812px">Carpentry</div>
<div class="abs service" style="left:81px;top:842px">Tile &amp; Flooring</div>
<div class="abs service" style="left:81px;top:872px">Decks</div>
<div class="abs service" style="left:266px;top:752px">General Home Maintenance</div>
<div class="abs service" style="left:266px;top:782px">Painting &amp; Wall Treatments</div>
<div class="abs service" style="left:266px;top:812px">Drywall Install</div>
<div class="abs service" style="left:266px;top:842px">Electrical</div>
<div class="abs service" style="left:266px;top:872px">Fences</div>

<aside>
  <div class="abs newsletter">
    <h4>OUR NEWSLETTER</h4>
    <p>Get your Regular Email for Recieving the Update News and Events.</p>
    <div class="field"><span>Enter Your Email..</span><b>GO</b></div>
  </div>
  <div class="abs quote-card"></div>
  <div class="abs quote-figure" role="img" aria-label="Photo of a businessman in a suit offering a handshake"></div>
  <div class="abs quote-icon"><svg width="14" height="14" viewBox="0 0 14 14"><rect x="1" y="3" width="9" height="10" fill="none" stroke="#fff" stroke-width="1.4"/><path d="M5 9l1-3 6-6 2 2-6 6z" fill="#fff"/></svg></div>
  <div class="abs quote-bar">QUICK QUOTE FORM</div>
  <div class="abs contact">
    <svg class="abs" style="left:10px;top:7px" width="13" height="10"><rect width="13" height="10" fill="#fff"/><path d="M0 0l6.5 5L13 0" fill="none" stroke="#e4ad06"/></svg>
    <h4>CONTACT US TODAY!</h4>
    <div class="lead">501 LOREM IPSUM IS<br>SIMPLY DUMMY TEXT.</div>
    <div class="small">Find out more our services Call:</div>
    <div class="phone">03 9024-7716</div>
  </div>
</aside>

<section class="abs testimonials"><h2>TESTIMONIALS</h2></section>
<div class="abs bubble" style="left:81px"><span class="quote-mark" style="left:8px;top:6px">“</span><h5>LOREM IPSUM DOLOR SIT AMET</h5><p>Lorem ipsum dolor sit amet, consectetur adipisicing elit, sed do eiusmod tempor incididunt ut labore et dolore magna aliqua.</p><span class="quote-mark" style="right:8px;bottom:2px">”</span></div>
<div class="abs bubble" style="left:356px"><span class="quote-mark" style="left:8px;top:6px">“</span><h5>LOREM IPSUM DOLOR SIT AMET</h5><p>Lorem ipsum dolor sit amet, consectetur adipisicing elit, sed do eiusmod tempor incididunt ut labore et dolore magna aliqua.</p><span class="quote-mark" style="right:8px;bottom:2px">”</span></div>
<div class="abs avatar" style="left:82px"><div role="img" aria-label="Client portrait photo"></div></div>
<div class="abs client" style="left:134px">-CLIENTS NAME</div>
<div class="abs avatar" style="left:357px"><div role="img" aria-label="Client portrait photo"></div></div>
<div class="abs client" style="left:409px">-CLIENTS NAME</div>

<footer class="abs footer"></footer>
<div class="abs seal" role="img" aria-label="Quality seal badge"></div>
<div class="abs follow">
  <h4>Follow Us</h4>
  <ul><li><i></i>Linkhub</li><li><i></i>Facenote</li><li><i></i>Chirper</li></ul>
</div>
<nav class="abs foot-nav"><a href="#">Home</a><a href="#">Steelshade</a><a href="#">Instant Quote</a><a href="#">Gallery</a><a href="#">Products &amp; Services</a><a href="#">Contact us</a></nav>
<div class="abs copy">© 2013 Tall Gum Fencing. All Rights Reserved</div>

</body>
</html>
```